Business card design/logo/website name

I am a business coach. My business name is KDP (Kessel Dunmore & Partners, Inc.) I want to use this card just for coaching. I do two kinds: Personal Image coach and Executive business coach
1. I work with people to become a polished global professional.
"Become a confident, savvy professional building relationships tactfully and appropriately while clearly representing your own company’s message and image.
Learn the nuances… Master the skills… Use the business etiquette techniques and protocols that allow you to seamlessly and confidently conduct business in a global business environment.
Have the comfort of knowing what to expect, what to do and how to easily build long and short-term relationships that give you the winning edge and increased company profits."
2. Leadership Coaching
For increasing the team’s productivity by building stronger relationships. Build strong compelling vision and write and share their Personal Leadership Philosophy, a roadmap that is concise and commanding and gives the team a clear vision of the leader's expectations.
Updates

KDP should be the logo. (Downplay the Kessel Dunmore and Partners, Inc.)

Want:
Executive Coach
Consultant

Reason: I am traveling and connections are often broken.

Target Market(s)

Executives, business people

Industry/Entity Type

Building

Font styles to use
Sans Serif
Script

Colors
0255a3
3176b5
85acd3
ec2027

Requirements
Must have
• KDP as the logo,(no preference on how you treat KDP) with Kessel Dunmore & Partners. Inc. downplayed.
On the card:
Rosalind Dunmore CEO
Executive Coach
Consultant
KRC 4(c)
Coaching - Training - Strategic Planning

```html
<!DOCTYPE html>
<html lang="en">
<head>
<meta charset="utf-8">
<title>KDP Business Card</title>
<link rel="stylesheet" href="https://fonts.googleapis.com/css2?family=Arimo:wght@400;700&display=swap">
<style>
  :root {
    --backdrop: #34403f;
    --card: #fbfcfd;
    --brand-blue: #0255a3;
    --band-blue: #2d5fa8;
    --navy: #1d3570;
    --orange: #f26522;
    --orange-deep: #d8442a;
    --orange-soft: #ef5b24;
    --ornament: #e9ebef;
  }
  * { box-sizing: border-box; margin: 0; padding: 0; }
  html, body { width: 1200px; height: 1000px; overflow: hidden; }
  body {
    background: var(--backdrop);
    font-family: "Arimo", Arial, sans-serif;
    position: relative;
  }
  .card {
    position: absolute;
    left: 280px;
    width: 640px;
    height: 366px;
    background: var(--card);
    overflow: hidden;
    box-shadow: 0 14px 30px rgba(0,0,0,0.45);
  }
  .card--front { top: 90px; }
  .card--back { top: 544px; }
  .card__bands { position: absolute; inset: 0; width: 640px; height: 366px; }
  .ornament {
    position: absolute;
    border-radius: 50%;
    background: radial-gradient(circle, rgba(233,235,239,0.2) 0%, var(--ornament) 55%, rgba(233,235,239,0) 72%);
  }
  .card--front .ornament { left: 150px; top: 20px; width: 240px; height: 240px; }
  .card--back .ornament { left: 110px; top: 45px; width: 270px; height: 270px; }
  .brand { position: absolute; }
  .brand__mark {
    font-weight: 700;
    color: var(--brand-blue);
    letter-spacing: 1px;
    line-height: 1;
  }
  .brand__company {
    color: var(--orange);
    font-size: 11px;
    font-weight: 700;
    text-transform: uppercase;
    letter-spacing: 0.2px;
    margin-top: 2px;
    white-space: nowrap;
  }
  .card--front .brand { left: 40px; top: 30px; }
  .card--front .brand__mark { font-size: 72px; }
  .card--back .brand { left: 140px; top: 112px; }
  .card--back .brand__mark { font-size: 88px; }
  .card--back .brand__company { font-size: 11.5px; margin-top: 4px; }
  .person { position: absolute; left: 60px; top: 128px; color: var(--navy); }
  .person__name { font-size: 24px; font-weight: 700; }
  .person__title { font-size: 17px; font-weight: 700; margin-top: 2px; }
  .person__services { font-size: 16px; margin-top: 10px; color: #2a3f78; }
  .contact { list-style: none; margin-top: 10px; font-size: 13.5px; font-weight: 700; color: var(--navy); }
  .contact__item { display: flex; align-items: flex-start; gap: 7px; line-height: 1.25; margin-bottom: 2px; }
  .contact__icon { width: 11px; height: 11px; margin-top: 2px; flex: none; fill: var(--navy); }
</style>
</head>
<body>

<section class="card card--front" aria-label="Business card front">
  <div class="ornament" role="img" aria-label="Faint circular guilloche ornament"></div>
  <svg class="card__bands" viewBox="0 0 640 366" aria-hidden="true">
    <polygon points="545,0 600,0 360,366 300,366" fill="var(--band-blue)"/>
    <polygon points="600,0 640,0 640,366 360,366" fill="var(--orange-soft)"/>
    <polygon points="640,40 640,366 420,366" fill="var(--orange-deep)"/>
  </svg>
  <div class="brand">
    <div class="brand__mark">KDP</div>
    <div class="brand__company">Kessel Dunmore &amp; Partners, Inc</div>
  </div>
  <div class="person">
    <p class="person__name">Rosalind L. Dunmore, CEO</p>
    <p class="person__title">Global Executive Coach</p>
    <p class="person__services">Training, Coaching, Diversity, Protocol</p>
    <ul class="contact">
      <li class="contact__item">
        <svg class="contact__icon" viewBox="0 0 12 12"><path d="M6 1 L11.5 6 H10 V11 H7 V8 H5 V11 H2 V6 H0.5 Z"/></svg>
        <span>2240 Harbor Ridge Dr, Brookfield,<br>WI 53045, United States</span>
      </li>
      <li class="contact__item">
        <svg class="contact__icon" viewBox="0 0 12 12"><path d="M1 4 Q6 0 11 4 L10 6 L8 5 L8 4 Q6 3 4 4 L4 5 L2 6 Z M3 7 H9 L10 11 H2 Z"/></svg>
        <span>(555) 214-0387</span>
      </li>
      <li class="contact__item">
        <svg class="contact__icon" viewBox="0 0 12 12"><path d="M1 2.5 H11 V9.5 H1 Z M1.5 3 L6 6.5 L10.5 3 V3.2 L6 7.2 L1.5 3.2 Z" fill-rule="evenodd"/></svg>
        <span>rdunmore@kesseldunmore.com</span>
      </li>
      <li class="contact__item">
        <svg class="contact__icon" viewBox="0 0 12 12"><path d="M4.5 7.5 L7.5 4.5 M5 3 L6.5 1.5 Q8 0 10 2 Q12 4 10.5 5.5 L9 7 M7 9 L5.5 10.5 Q4 12 2 10 Q0 8 1.5 6.5 L3 5" stroke="var(--navy)" stroke-width="1.4" fill="none"/></svg>
        <span>kesseldunmore.com</span>
      </li>
    </ul>
  </div>
</section>

<section class="card card--back" aria-label="Business card back">
  <div class="ornament" role="img" aria-label="Faint circular guilloche ornament"></div>
  <svg class="card__bands" viewBox="0 0 640 366" aria-hidden="true">
    <polygon points="550,0 600,0 360,366 305,366" fill="var(--band-blue)"/>
    <polygon points="600,0 640,0 640,366 360,366" fill="var(--orange-soft)"/>
    <polygon points="640,40 640,366 420,366" fill="var(--orange-deep)"/>
  </svg>
  <div class="brand">
    <div class="brand__mark">KDP</div>
    <div class="brand__company">Kessel Dunmore &amp; Partners, Inc</div>
  </div>
</section>

</body>
</html>
```